Wine Bottle Label for Tall Fern Wines

We are a small, newly established winery in need of an original, bold and outstanding bottle label design for our Tall Fern wine.

Our vineyard and winery are located on a 200 acre farm in a remote part of southern Oregon. The name "Tall Fern" was inspired by the large, overgrown size of all of the foliage here, including our grapevines. Things grow large and vigorous in Oregon! And everything is very lush and green. It is almost surreal or other-worldly, like the landscapes seen in the Keeper of The Stones movies, or the land of Quill. It is a place that makes you say "wow" with its epic, large scale, natural beauty.

The name "Tall Fern" also captures the essence of our wine. It is big in flavor, quality and color. Our first release is a Pinot Noir (red). Pinot Noir wines often are subtle in flavor and thin in their color. Our label should convey that our Pinot Noir is a much more robust, darker, heavier, meatier, more flavorful wine that is a lot more fun than an "ordinary" wine. At the same time, this wine is not cheap, and so nothing in the label should convey "bargain," "low price," or "cheapness." This is a fine wine with a sense of adventure. Be sure to convey "quality" with your design along with "big," "adventure" and "fun".

The label should appeal to a younger demographic, both male and female, between the ages of 21 and 35. It should be non-traditional and adventurous and suggest a pushing of boundaries and a breaking of rules. This Pinot Noir does not conform to the normal "limitations" of the variety, therefore the label should not conform. It should have an "organic" or "natural" or "agricultural" vibe, as opposed to something mechanical or technical. It should, however, be contemporary. Do not confuse "natural" or "organic" with being nostalgic or old school. Think "agri-hipsters."

The label should be designed to fit on a Burgundy-style wine bottle (photo attached for reference). (Note: All Pinot Noir and Chardonnay is bottled in Burgundy bottles, If you are not sure about the bottle shape you can go to a local store and compare the various bottles. Locate a bottle of Pinot Noir or Chardonnay or anything identified as a "Burgundy Wine," and it should be the correct bottle. The tall, skinny bottles used for Cabernet Sauvignon are NOT correct)). Please see the "Must Have" notes for more on the bottle.

In summary, the final project should be a wine bottle label design that conveys bigness, vastness, adventurous, non-traditional, high quality wine. A good tagline to keep in mind is "Living Large."

Target Market(s)

Young, hip, non-conformist wine drinkers aged 21-35 with a sense of adventure and an appreciation of quality.

Industry/Entity Type

School

Requirements
Must have
• *Must contain the words:

Tall Fern (the brand)
2013 Pinot Noir (the vintage year and variety)

*The label must be designed to fit a Burgundy-style wine bottle. A photo is attached for reference.

*Additionally, the label needs to fit on the lower, widest part of the bottle. The label will be printed on sticky paper and rolled onto the bottle with a machine. The machine cannot apply labels to the neck of the bottle. The maximum size of a label that will fit this space is 5.5 inches wide by 4.5 inches tall. You DO NOT have to fill ALL of this space or confine the label shape to a rectangle, but the label cannot exceed this size or it won't stick to the bottle properly. It will really help if you can put your hands on an actual bottle to see the logistics of applying the label. But if that is not possible, just do your best with the instructions you have. I am confident the winning design could be adjusted to fit the bottle, if necessary
Nice to have
• *Wine grape leaf or leaves.

*A concept I have been playing with is sunlight shining through leaves like light through a Marlowe lamp or a stained glass window. This is NOT a requirement for this label. However, if the concept inspires and idea, I would be most happy to see it.
Should not have
• IF a leaf or leaves are included in the design (not a requirement) they MUST be wine grapevine leafs and preferably leaves of the Pinot Noir vine. Do not use generic leaves or identifiable leaves such as oak leaves, maple leaves, or anything that looks like the Canadian flag or the Halden Ridge Ravens hockey logo. Reference the attached photos of wine grape leaves to see the correct leaf type. I am happy to email more photos upon request. These photos may be used in whole or in part in your design, however, a leaf from a photo is NOT a requirement, nor is the image of a leaf or leaves.

This label should NOT be designed for Bordeaux-style wine bottles (the tall, skinny ones).

```html
<!DOCTYPE html>
<html lang="en">
<head>
<meta charset="utf-8">
<title>Tall Fern Wines – 2013 Pinot Noir Label</title>
<link rel="stylesheet" href="https://fonts.googleapis.com/css2?family=Cinzel:wght@400&family=Mrs+Saint+Delafield&family=Roboto+Condensed:wght@400&display=swap">
<style>
  :root {
    --page: #ffffff;
    --label: #2c2c2d;
    --label-deep: #232324;
    --label-edge: #383839;
    --gold: #b99442;
    --grey-text: #8d8d8d;
    --pattern-a: #303031;
    --pattern-b: #262627;
  }
  html, body {
    margin: 0;
    width: 1200px;
    height: 900px;
    overflow: hidden;
    background: var(--page);
  }
  .canvas {
    position: relative;
    width: 1200px;
    height: 900px;
  }
  .wine-label {
    position: absolute;
    left: 330px;
    top: 105px;
    width: 540px;
    height: 690px;
    background: var(--label);
    overflow: hidden;
  }
  .label-shapes {
    position: absolute;
    inset: 0;
  }
  .brand-name {
    position: absolute;
    left: 0;
    right: 0;
    top: 120px;
    margin: 0;
    text-align: center;
    font-family: "Cinzel", serif;
    font-weight: 400;
    font-size: 56px;
    line-height: 1;
    letter-spacing: 6px;
    color: var(--gold);
  }
  .vintage {
    position: absolute;
    left: 0;
    right: 0;
    top: 292px;
    margin: 0;
    text-align: center;
    font-family: "Cinzel", serif;
    font-weight: 400;
    font-size: 68px;
    color: var(--gold);
  }
  .variety {
    position: absolute;
    left: 0;
    right: 0;
    top: 390px;
    margin: 0;
    text-align: center;
    font-family: "Cinzel", serif;
    font-weight: 400;
    font-size: 33px;
    letter-spacing: 10px;
    color: var(--gold);
  }
  .text-texture {
    position: absolute;
    left: 0;
    right: 0;
    top: 440px;
    height: 200px;
    background: repeating-linear-gradient(0deg, var(--pattern-a) 0 14px, var(--pattern-b) 14px 28px);
    opacity: 0.9;
  }
  .origin-intro {
    position: absolute;
    left: 0;
    right: 0;
    top: 478px;
    margin: 0;
    text-align: center;
    font-family: "Cinzel", serif;
    font-size: 15px;
    letter-spacing: 3px;
    color: var(--grey-text);
  }
  .origin-region {
    position: absolute;
    left: 0;
    right: 0;
    top: 500px;
    margin: 0;
    text-align: center;
    font-family: "Mrs Saint Delafield", cursive;
    font-size: 58px;
    color: var(--gold);
  }
  .legal-line {
    position: absolute;
    left: 22px;
    right: 22px;
    bottom: 22px;
    display: flex;
    justify-content: space-between;
    font-family: "Roboto Condensed", sans-serif;
    font-size: 16px;
    color: var(--grey-text);
  }
</style>
</head>
<body>
<main class="canvas">
  <article class="wine-label" aria-label="Tall Fern 2013 Pinot Noir wine label">
    <svg class="label-shapes" width="540" height="690" viewBox="0 0 540 690" aria-hidden="true">
      <polygon points="360,0 540,0 540,440 470,440" fill="var(--label-deep)"/>
      <path d="M -10 300 Q 270 225 560 262" fill="none" stroke="var(--label-edge)" stroke-width="3"/>
      <line x1="0" y1="440" x2="540" y2="440" stroke="var(--label-edge)" stroke-width="1"/>
    </svg>
    <h1 class="brand-name">TALL FERN</h1>
    <p class="vintage">2013</p>
    <p class="variety">PINOT NOIR</p>
    <div class="text-texture" role="img" aria-label="Faint repeating lettering texture of vintage, variety and region names"></div>
    <p class="origin-intro">PRODUCT FROM</p>
    <p class="origin-region">Southern Oregon</p>
    <div class="legal-line">
      <span class="alcohol">ALC. 13.5% BY VOL.</span>
      <span class="volume">750ML</span>
    </div>
  </article>
</main>
</body>
</html>
```